Fresh, modern, fun business card for pediatric dental practice

Need a business card for fresh, modern, fun pediatric dental practice

Clean look that matches our website's font and colors

We prefer the look of curved corners on business cards

Target Market(s)

parents (mothers) of young children, professionals, mid-high class

Industry/Entity Type

Dental

Contact Information for Business Card

Maplebrook Pediatric Dentistry
482 Quarry Lane
Suite 517
Fernhill, PA 17599
717.555.0193
www.maplebrookkidsdental.example

Mei-Ran Tsai, DMD
Corinne Walbeck, DMD
(we are working on our email address, but we would like that on the card as well)

Font styles to use
Sans Serif

Requirements
Must have
• All info; we would also like to make cards for individual staff members
• colors from our website and color palatte, attatched
• use same font and design as website for branding
Nice to have
• clean, simple card that has a pop of color
• we would like to see a few designs with our tag line "where smiles get brighter"
• we are not sure if we want to have it on there or not
• we would like to see a few designs incorporating the ribbon graphic on our website where the word WELCOME is

```html
<!DOCTYPE html>
<html lang="en">
<head>
<meta charset="utf-8">
<title>Maplebrook Pediatric Dentistry – Business Card</title>
<link rel="stylesheet" href="https://fonts.googleapis.com/css2?family=Work+Sans:wght@300;400;500;600&display=swap">
<style>
  :root {
    --sun-yellow: #fdb71a;
    --photo-yellow: #f2bc3f;
    --berry: #c7289a;
    --paper: #ffffff;
    --backdrop: #3f3a35;
  }
  * { box-sizing: border-box; margin: 0; padding: 0; }
  html, body { width: 1200px; height: 930px; overflow: hidden; }
  body {
    background: var(--backdrop);
    font-family: "Work Sans", Arial, sans-serif;
    position: relative;
  }
  .card {
    position: absolute;
    left: 278px;
    width: 644px;
    height: 368px;
    border-radius: 24px;
    overflow: hidden;
  }
  .card--front { top: 76px; background: var(--sun-yellow); }
  .card--back { top: 486px; background: var(--photo-yellow); }

  .front-swoosh { position: absolute; inset: 0; }

  .brand {
    position: absolute;
    text-align: center;
    line-height: 1;
  }
  .brand__dot {
    display: block;
    border-radius: 50%;
    margin: 0 auto;
  }
  .brand__name { font-weight: 500; }
  .brand__tag { font-weight: 400; }

  .brand--front {
    left: 330px; width: 300px; top: 52px;
    color: var(--sun-yellow);
  }
  .brand--front .brand__dot {
    width: 44px; height: 44px;
    border: 4px solid var(--sun-yellow);
    margin-bottom: 22px;
  }
  .brand--front .brand__name { font-size: 44px; letter-spacing: 2px; }
  .brand--front .brand__tag { font-size: 21px; letter-spacing: 2.5px; margin-top: 8px; color: var(--berry); }

  .contact {
    position: absolute;
    left: 30px; top: 184px;
    color: var(--paper);
  }
  .contact__name { font-size: 23px; font-weight: 600; letter-spacing: 0.3px; line-height: 28px; }
  .contact__title { font-size: 15px; font-weight: 300; line-height: 18px; }
  .contact__address { font-size: 15px; font-weight: 300; line-height: 19px; margin-top: 12px; }
  .contact__list { list-style: none; font-size: 15px; font-weight: 300; line-height: 19px; margin-top: 8px; }
  .contact__list li { display: flex; align-items: center; gap: 7px; }
  .contact__list svg { width: 10px; height: 10px; flex: none; }

  .back-photo { position: absolute; inset: 0; background: radial-gradient(ellipse at 50% 40%, #e7ad35 0%, var(--photo-yellow) 70%); }
  .brand--back {
    left: 0; right: 0; top: 106px;
    color: var(--paper);
  }
  .brand--back .brand__dot {
    width: 62px; height: 62px;
    border: 5px solid var(--paper);
    margin-bottom: 30px;
  }
  .brand--back .brand__name { font-size: 58px; letter-spacing: 3px; }
  .brand--back .brand__tag { font-size: 28px; letter-spacing: 3px; margin-top: 8px; }
</style>
</head>
<body>

<section class="card card--front">
  <svg class="front-swoosh" viewBox="0 0 644 368" aria-hidden="true">
    <path d="M218 0 C 236 190, 410 318, 610 368 L 644 368 L 644 0 Z" fill="var(--berry)"/>
    <path d="M221 0 C 239 188, 412 316, 612 368" fill="none" stroke="var(--paper)" stroke-width="2"/>
    <path d="M244 0 C 250 200, 430 330, 622 368 L 644 368 L 644 0 Z" fill="var(--paper)"/>
  </svg>

  <div class="brand brand--front">
    <span class="brand__dot"></span>
    <div class="brand__name">maplebrook</div>
    <div class="brand__tag">pediatric dentistry</div>
  </div>

  <div class="contact">
    <h1 class="contact__name">CORINNE WALBECK</h1>
    <p class="contact__title">DMD</p>
    <p class="contact__address">482 Quarry Lane<br>Suite 517 Fernhill, PA 17599</p>
    <ul class="contact__list">
      <li><svg viewBox="0 0 10 10"><path d="M2 1 L4 1 L4.5 3 L3.3 3.8 C3.8 5 4.8 6 6 6.6 L6.8 5.5 L9 6 L9 8 C9 8.6 8.5 9 8 9 C4.5 9 1 5.5 1 2 C1 1.4 1.4 1 2 1 Z" fill="var(--paper)"/></svg>717.555.0193</li>
      <li><svg viewBox="0 0 10 10"><rect x="0.8" y="2" width="8.4" height="6" fill="none" stroke="var(--paper)" stroke-width="1"/><path d="M0.8 2 L5 5.5 L9.2 2" fill="none" stroke="var(--paper)" stroke-width="1"/></svg>hello@maplebrookkids.example</li>
      <li><svg viewBox="0 0 10 10"><circle cx="5" cy="5" r="4" fill="none" stroke="var(--paper)" stroke-width="1"/><ellipse cx="5" cy="5" rx="1.8" ry="4" fill="none" stroke="var(--paper)" stroke-width="0.8"/><line x1="1" y1="5" x2="9" y2="5" stroke="var(--paper)" stroke-width="0.8"/></svg>www.maplebrookkidsdental.example</li>
    </ul>
  </div>
</section>

<section class="card card--back">
  <div class="back-photo" role="img" aria-label="Yellow-tinted photo of a smiling young child with pigtails brushing her teeth"></div>
  <div class="brand brand--back">
    <span class="brand__dot"></span>
    <div class="brand__name">maplebrook</div>
    <div class="brand__tag">pediatric dentistry</div>
  </div>
</section>

</body>
</html>
```